Black Car Limousine transportation business in Naples Florida

Always stand for my reliability and RVD stands for Love, K and M are the first initials of my children's names. It should show professionalism and a dedication to customer service. We keep our clients identities private. Show our professionalism. We are Black car Black tie company. We service transportation on a reserve basis to and from residents, airports, casinos, hotels,

Target Market(s)

It is a Private car service. High end clients. Businesses, Celebrity and athletes. Service to airports, hotels, special events.

Industry/Entity Type

Business

Contact Information for Business Card

A pearl metallic or Luster card. Standard business card size. Would like the name, Company email, show we take credit cards and phone number. Currently I don't have a website but will like to add later.

Logo Text

STEADFAST RVD TRANSPORTATION

Font styles to use
Serif

Colors
eaeaea
000000

Requirements
Must have
• Must have Company email, show we take credit cards and phone number. Currently I don't have a website but will like to add later.
Nice to have
• Would like to stay with a black and white theme. Open to some color trim.
Should not have
• Open to suggestions

```html
<!DOCTYPE html>
<html lang="en">
<head>
<meta charset="utf-8">
<title>Steadfast RVD Transportation – Business Card</title>
<link rel="stylesheet" href="https://fonts.googleapis.com/css2?family=Lora:wght@400;600&display=swap">
<style>
  :root {
    --backdrop: #d9d6d3;
    --card-dark-top: #262626;
    --card-dark-mid: #3a3a3a;
    --card-dark-bottom: #8d8d8d;
    --card-light: #eaeaea;
    --ink-white: #ffffff;
    --ink-black: #000000;
    --vehicle-dark: #0e0e0e;
    --vehicle-sheen: #3c3c3c;
    --icon-cut: #3a3a3a;
  }
  * { margin: 0; padding: 0; box-sizing: border-box; }
  html, body {
    width: 1200px;
    height: 900px;
    overflow: hidden;
    background: var(--backdrop);
    font-family: "Lora", serif;
  }
  .canvas { position: relative; width: 1200px; height: 900px; }

  .card { position: absolute; width: 556px; height: 343px; overflow: hidden; }

  /* Front side */
  .card-front {
    left: 238px; top: 61px;
    background: linear-gradient(180deg, var(--card-dark-top) 0%, var(--card-dark-mid) 45%, var(--card-dark-bottom) 100%);
    color: var(--ink-white);
  }
  .holder { position: absolute; left: 26px; top: 40px; }
  .holder-name { font-size: 19px; font-weight: 600; line-height: 24px; }
  .holder-title { font-size: 14.5px; font-weight: 400; line-height: 20px; }

  .contact-list { position: absolute; left: 26px; top: 172px; list-style: none; }
  .contact-item {
    display: flex; align-items: center; gap: 9px;
    font-size: 14.5px; line-height: 20px;
  }
  .contact-item svg { width: 11px; height: 11px; fill: var(--ink-white); flex: none; }

  .address { position: absolute; left: 26px; top: 255px; font-size: 14.5px; line-height: 20px; font-style: normal; }

  .vehicle-photo {
    position: absolute; left: 247px; top: 114px; width: 309px; height: 229px;
    background:
      radial-gradient(ellipse 75% 55% at 62% 48%, var(--vehicle-sheen) 0%, var(--vehicle-dark) 45%, rgba(14,14,14,0) 100%),
      linear-gradient(180deg, rgba(0,0,0,0) 78%, rgba(225,225,225,0.4) 100%);
  }

  /* Back side */
  .card-back {
    left: 457px; top: 518px; width: 560px;
    background: var(--card-light);
  }
  .brand {
    position: absolute; left: 0; right: 0; top: 92px;
    text-align: center; color: var(--ink-black);
    font-family: "Lora", serif; font-weight: 400;
    line-height: 1;
  }
  .brand-line { display: block; }
  .brand-top { font-size: 24px; letter-spacing: 3px; margin-bottom: 4px; }
  .brand-core { font-size: 86px; letter-spacing: 6px; }
  .brand-bottom { font-size: 27px; letter-spacing: 1px; margin-top: 6px; }
</style>
</head>
<body>
<main class="canvas">

  <section class="card card-front" aria-label="Business card front">
    <div class="holder">
      <p class="holder-name">Daniel Whitford</p>
      <p class="holder-title">Managing Director</p>
    </div>

    <ul class="contact-list">
      <li class="contact-item">
        <svg viewBox="0 0 12 12" aria-hidden="true"><path d="M2.4 0.6l1.8 2.2-1 1.2c.6 1.5 1.8 2.7 3.3 3.3l1.2-1 2.2 1.8-.9 2.2C4.8 10.2 1.8 7.2 0.6 1.5z"/></svg>
        <span>044-987 654 321</span>
      </li>
      <li class="contact-item">
        <svg viewBox="0 0 12 12" aria-hidden="true"><path d="M1 3h10v6.5H1z M1 3l5 3.5L11 3" stroke="#3a3a3a" stroke-width="0.9"/></svg>
        <span>info@steadfastrvd.com</span>
      </li>
      <li class="contact-item">
        <svg viewBox="0 0 12 12" aria-hidden="true"><rect x="0.5" y="2" width="11" height="8" rx="1.2"/><rect x="0.5" y="4" width="11" height="1.6" fill="#3a3a3a"/></svg>
        <span>Major credit cards accepted</span>
      </li>
    </ul>

    <address class="address">
      4810, Harbor Lane North<br>
      Naples, Florida 34102.
    </address>

    <div class="vehicle-photo" role="img" aria-label="Photograph of a black luxury SUV, front three-quarter view"></div>
  </section>

  <section class="card card-back" aria-label="Business card back">
    <p class="brand">
      <span class="brand-line brand-top">STEADFAST</span>
      <span class="brand-line brand-core">RVD</span>
      <span class="brand-line brand-bottom">TRANSPORTATION</span>
    </p>
  </section>

</main>
</body>
</html>
```